Global (re)insurance broker needs a business card design

We need a classic business card for our company that is headquartered in SG, with offices in Malaysia and Dubai. We specialise in insurance and reinsurance broking and consultancy for our global clients.

```html
<!DOCTYPE html>
<html lang="en">
<head>
<meta charset="utf-8">
<title>Varlow – Business Card</title>
<link rel="stylesheet" href="https://fonts.googleapis.com/css2?family=Open+Sans:wght@400;600&family=Nunito:wght@600&display=swap">
<style>
  :root {
    --stage: #2b2b2e;
    --card: #1e1e22;
    --card-back: #151517;
    --brand-blue: #2f4fa8;
    --brand-sage: #b9d3b1;
    --ink-light: #f2f2f2;
    --pattern-dark: #1c1c1f;
    --pattern-light: #3a3a3e;
  }
  * { box-sizing: border-box; margin: 0; padding: 0; }
  html, body { width: 1200px; height: 780px; overflow: hidden; }
  body {
    background: var(--stage);
    font-family: "Open Sans", Arial, sans-serif;
    position: relative;
  }
  .card {
    position: absolute;
    top: 241px;
    width: 520px;
    height: 298px;
    border-radius: 4px;
    overflow: hidden;
  }
  .card--front { left: 50px; background: var(--card); }
  .card--back { left: 630px; background: var(--card-back); }

  .holder { position: absolute; left: 28px; top: 26px; }
  .holder__name {
    font-family: "Nunito", "Open Sans", sans-serif;
    font-weight: 600;
    font-size: 30px;
    line-height: 1;
    padding-left: 10px;
    border-left: 6px solid var(--brand-blue);
    margin-left: -16px;
  }
  .holder__first { color: var(--brand-blue); }
  .holder__last { color: var(--brand-sage); }
  .holder__title { color: var(--ink-light); font-size: 13px; margin-top: 4px; }

  .wordmark {
    position: absolute;
    right: 28px;
    top: 112px;
    font-family: "Nunito", "Open Sans", sans-serif;
    font-weight: 600;
    font-size: 70px;
    letter-spacing: 2px;
    color: var(--brand-sage);
    line-height: 1;
  }

  .contacts {
    position: absolute;
    left: 28px;
    bottom: 26px;
    list-style: none;
    color: var(--ink-light);
    font-size: 12.5px;
    line-height: 18px;
  }
  .contacts li { display: flex; align-items: center; gap: 8px; }
  .contacts svg { width: 12px; height: 12px; flex: none; }

  .address {
    position: absolute;
    right: 28px;
    bottom: 26px;
    color: var(--ink-light);
    font-size: 13px;
    line-height: 18px;
    text-align: right;
    font-style: normal;
  }

  .back__pattern {
    position: absolute;
    inset: 0;
    background: linear-gradient(115deg, var(--pattern-dark) 0%, var(--pattern-dark) 55%, var(--pattern-light) 100%);
  }
  .back__mark {
    position: absolute;
    left: 50%;
    top: 50%;
    transform: translate(-50%, -50%);
    font-family: "Nunito", "Open Sans", sans-serif;
    font-weight: 600;
    font-size: 16px;
    letter-spacing: 1px;
    color: var(--brand-sage);
  }
</style>
</head>
<body>
  <section class="card card--front" aria-label="Business card front">
    <div class="holder">
      <p class="holder__name"><span class="holder__first">Mira</span> <span class="holder__last">Holt</span></p>
      <p class="holder__title">Chief Operating Officer</p>
    </div>

    <p class="wordmark">VARLOW</p>

    <ul class="contacts">
      <li>
        <svg viewBox="0 0 12 12" aria-hidden="true"><rect x="3" y="0.5" width="6" height="11" rx="1" fill="none" stroke="#b9d3b1" stroke-width="1"/></svg>
        +65 8124 5036
      </li>
      <li>
        <svg viewBox="0 0 12 12" aria-hidden="true"><circle cx="6" cy="6" r="5.5" fill="#2f4fa8"/><path d="M0.5 6h11M6 0.5c-2.5 3-2.5 8 0 11M6 0.5c2.5 3 2.5 8 0 11" fill="none" stroke="#1e1e22" stroke-width="0.8"/></svg>
        www.varlow.com
      </li>
      <li>
        <svg viewBox="0 0 12 12" aria-hidden="true"><rect x="0.5" y="2.5" width="11" height="8" fill="#b9d3b1"/><path d="M0.5 2.5l5.5 4.5 5.5-4.5" fill="none" stroke="#1e1e22" stroke-width="0.9"/></svg>
        mira@varlow.com
      </li>
    </ul>

    <address class="address">
      22 Harbour Lane, Meridian<br>
      Tower #08-04, Singapore 018925
    </address>
  </section>

  <section class="card card--back" aria-label="Business card back">
    <div class="back__pattern" role="img" aria-label="Repeating brand name pattern in glossy dark tones"></div>
    <p class="back__mark">VARLOW</p>
  </section>
</body>
</html>
```